Business card design for holistic health care clinic

We need a double-sided business card design for our holistic health care clinic that integrates our logo design and also its color scheme. My business is called Valmira. It is an integrative medicine clinic. You have already done the logo for me. Please ensure an elegant and upscale design that is not cluttered, but still has all the necessary information (please see below for details).

Target Market(s)

Wellness, fitness, rehabilitation for educated, well-traveled open-minded clients who are focused on natural, organic, balanced and preventive healthcare and lifestyle.

Industry/Entity Type

Medical

Contact Information for Business Card

Modern, clean.

Number of Pages Required

1 page

Font styles to use
Serif
Sans Serif

Colors

Designer to choose colors to be used in the design.

Requirements
Must have
• Logo on one side, all other information on the other side.
• Other information should include:
• Tobias Wrenfeld - DOE, CPT, LMT
• 4100 East Marrow Drive
• Austin, TX 78119
• 512 555 0148
• 818 555 0192
• info@ValmiraHealth.example
• t.wrenfeld@ValmiraHealth.example
Nice to have
• Darker background on front - but not totally black - shaded/dark gray.

```html
<!DOCTYPE html>
<html lang="en">
<head>
<meta charset="utf-8">
<title>Valmira – Business Card</title>
<link href="https://fonts.googleapis.com/css2?family=PT+Sans:wght@400;700&display=swap" rel="stylesheet">
<style>
  :root {
    --backdrop: #4a413c;
    --card: #1d1e20;
    --card-edge: #26272a;
    --brand-blue: #1b8fd2;
    --text-light: #e4e6e8;
    --divider: #8a8d92;
  }
  * { box-sizing: border-box; margin: 0; padding: 0; }
  html, body {
    width: 1200px; height: 864px; overflow: hidden;
    background: var(--backdrop);
    font-family: "PT Sans", sans-serif;
  }
  .sheet {
    width: 1200px; height: 864px;
    display: flex; flex-direction: column; align-items: center; justify-content: center;
    gap: 56px;
  }
  .card {
    width: 620px; height: 354px;
    background: linear-gradient(160deg, var(--card-edge), var(--card) 60%);
    border-radius: 4px;
    box-shadow: 0 12px 30px rgba(0,0,0,.45);
    position: relative;
    color: var(--text-light);
    overflow: hidden;
  }
  .wordmark { display: flex; flex-direction: column; align-items: flex-start; }
  .wordmark__name {
    font-weight: 700; color: var(--brand-blue);
    letter-spacing: 2px; line-height: 1; text-transform: uppercase;
  }
  .wordmark__tagline { color: var(--brand-blue); font-weight: 400; line-height: 1.1; white-space: nowrap; }

  /* Front */
  .card--front { display: flex; flex-direction: column; align-items: center; justify-content: center; gap: 34px; }
  .card--front .wordmark__name { font-size: 74px; }
  .card--front .wordmark__tagline { font-size: 25px; margin-top: 4px; }
  .motto { font-size: 17px; color: var(--text-light); }

  /* Back */
  .card--back { display: flex; align-items: center; padding: 0 30px 0 38px; }
  .card--back .wordmark { width: 262px; flex: none; }
  .card--back .wordmark__name { font-size: 56px; }
  .card--back .wordmark__tagline { font-size: 19px; margin-top: 3px; }
  .divider { width: 1px; height: 170px; background: var(--divider); margin: 0 22px 0 20px; flex: none; }
  .contact { font-size: 16px; line-height: 1.32; white-space: nowrap; }
  .contact__name { color: var(--brand-blue); font-weight: 700; font-size: 18px; margin-bottom: 8px; }
  .contact__credentials { font-size: 12px; }
  .contact__address { margin-bottom: 4px; }
  .contact__row { display: flex; align-items: center; gap: 8px; }
  .contact__icon { width: 13px; height: 13px; flex: none; fill: var(--brand-blue); }
</style>
</head>
<body>
<main class="sheet">
  <section class="card card--front" aria-label="Card front">
    <div class="wordmark">
      <span class="wordmark__name">Valmira</span>
      <span class="wordmark__tagline">Integrative Holistic Medicine</span>
    </div>
    <p class="motto">it's all about you – your health, your objectives</p>
  </section>

  <section class="card card--back" aria-label="Card back">
    <div class="wordmark">
      <span class="wordmark__name">Valmira</span>
      <span class="wordmark__tagline">Integrative Holistic Medicine</span>
    </div>
    <div class="divider"></div>
    <div class="contact">
      <p class="contact__name">TOBIAS WRENFELD <span class="contact__credentials">- DOE, CPT, LMT</span></p>
      <p class="contact__address">4100 East Marrow Drive<br>Austin, TX 78119</p>
      <p class="contact__row">
        <svg class="contact__icon" viewBox="0 0 16 16" aria-hidden="true"><path d="M3.5 1l2.5 3-1.5 1.8c.9 2 2.5 3.6 4.7 4.7L11 9l3.5 2.5-1.3 2.8C7.6 14 2 8.4 1 3z"/></svg>
        512 555 0148
      </p>
      <p class="contact__row">
        <svg class="contact__icon" viewBox="0 0 16 16" aria-hidden="true"><path d="M4 0h8a1 1 0 0 1 1 1v14a1 1 0 0 1-1 1H4a1 1 0 0 1-1-1V1a1 1 0 0 1 1-1zm1 2v10h6V2z"/></svg>
        818 555 0192
      </p>
      <p class="contact__row">
        <svg class="contact__icon" viewBox="0 0 16 16" aria-hidden="true"><path d="M1 3h14v10H1zm1.5 1.2L8 8.5l5.5-4.3z"/></svg>
        t.wrenfeld@ValmiraHealth.example
      </p>
      <p class="contact__row">
        <svg class="contact__icon" viewBox="0 0 16 16" aria-hidden="true"><path d="M1 3h14v10H1zm1.5 1.2L8 8.5l5.5-4.3z"/></svg>
        info@ValmiraHealth.example
      </p>
    </div>
  </section>
</main>
</body>
</html>
```